International professional tennis coach needs a book cover design

This is my 2nd published book, the first one was a #1 on the best seller. I'm looking for a world class book cover design for this new book. The name of my first book was 5 Baseline Habits to Unlock Your Flow Rhythm, located on Bookvale.com

The title of the new book:

Title: The Craft of Rally Mastery
Subtitle: Developing a Strategic Advantage through Competitive Intelligence

I'm uploading our new CRAFT OF RALLY logo that I'd like for you to use as the centerpiece of the book design along with a 21st century design feel that incorporates what the book topic is below::

--> This book is about building competitive intelligence by using tennis data analytics to develop and expand a player's strategic advantage for match play. <--

The colors we would like to use are Blue, Yellow, and Green. These shades of these colors should be bold! (You will see the bold color examples of blues, yellows, and greens that I'm talking about in the logos that are attached here, especially the colors for my Racket GridDrill App logo.

I will upload the Racket GridDrill logo which should go somewhere on the back cover design (small size maybe in the bottom corner).

This book is revolutionary to the standard way of teaching tennis, it is based on a decade of recording and gathering tennis data analytics and then we created on-court practice games to develop better decision making in players for the competitive edge.

My websites are www.elevatedrillzone.com and www.craftofrallymastery.com

```html
<!DOCTYPE html>
<html lang="en">
<head>
<meta charset="utf-8">
<title>The Craft of Rally Mastery – Book Cover</title>
<link rel="stylesheet" href="https://fonts.googleapis.com/css2?family=Kanit:wght@800&family=Barlow:wght@600&family=Barlow+Semi+Condensed:wght@400;600;700&family=Saira+Condensed:wght@400&display=swap">
<style>
  :root {
    --stage: #f9b243;
    --paper: #ffffff;
    --blue: #0a72c8;
    --blue-deep: #005bb5;
    --blue-light: #12b0f0;
    --yellow: #f8c21c;
    --yellow-pale: #f7d98a;
    --ink: #1d1d1d;
    --ink-soft: #333333;
  }
  * { box-sizing: border-box; margin: 0; padding: 0; }
  html, body { width: 1200px; height: 1000px; overflow: hidden; }
  body { background: var(--stage); position: relative; }

  .cover { position: absolute; top: 86px; width: 497px; height: 771px; background: var(--paper); overflow: hidden; }

  /* Back cover */
  .back-cover { left: 79px; }
  .back-tagline {
    position: absolute; left: 37px; top: 32px; width: 430px;
    font: 600 13.4px/20px "Barlow", sans-serif;
    color: var(--blue); text-transform: uppercase;
  }
  .back-rule { position: absolute; left: 0; right: 0; top: 77px; height: 3px; background: var(--blue); }
  .blurb {
    position: absolute; left: 36px; top: 89px; width: 380px;
    font: 400 12.2px/14.7px "Saira Condensed", sans-serif; color: var(--ink);
  }
  .blurb p { margin-bottom: 9.8px; }
  .author-photo { position: absolute; left: 36px; width: 98px; height: 124px; }
  .author-photo.first { top: 361px; background: linear-gradient(160deg, #3c4a4a, #8a8f8c 55%, #2d2f33); }
  .author-photo.second { top: 524px; background: linear-gradient(160deg, #8fb6cf, #9c8474 55%, #2f3340); }
  .author-bio {
    position: absolute; left: 143px; width: 312px;
    font: 400 12.2px/15.4px "Saira Condensed", sans-serif; color: var(--ink);
  }
  .author-bio.first { top: 360px; }
  .author-bio.second { top: 524px; width: 302px; }
  .author-name { color: var(--blue); font-family: "Barlow Semi Condensed", sans-serif; font-weight: 600; }
  .app-mark { position: absolute; left: 33px; top: 655px; width: 100px; text-align: center; }
  .app-mark-dot { display: block; width: 38px; height: 38px; margin: 0 auto 5px; border-radius: 50%; background: var(--blue); }
  .app-mark-name { font: 700 11px/12px "Barlow Semi Condensed", sans-serif; color: var(--blue); }
  .back-links { position: absolute; left: 29px; top: 729px; font: 400 9.6px/12px "Barlow Semi Condensed", sans-serif; color: var(--blue); }

  /* Front cover */
  .front-cover { left: 637px; }
  .front-art { position: absolute; inset: 0; }
  .book-title {
    position: absolute; left: 59px; top: 108px;
    font: 800 59px/74px "Kanit", sans-serif; color: var(--blue);
    text-transform: uppercase;
  }
  .title-rule { position: absolute; left: 60px; top: 337px; width: 388px; height: 4px; background: var(--blue); }
  .book-subtitle {
    position: absolute; left: 60px; top: 354px; width: 430px;
    font: 700 30px/37px "Barlow Semi Condensed", sans-serif; color: var(--ink-soft);
    text-transform: uppercase; letter-spacing: 1.3px;
  }
  .book-authors {
    position: absolute; left: 118px; top: 548px; width: 260px; text-align: center;
    font: 400 19px/24px "Barlow Semi Condensed", sans-serif; color: var(--blue);
    text-transform: uppercase; letter-spacing: 0.4px;
  }
</style>
</head>
<body>

<section class="cover back-cover" aria-label="Back cover">
  <h2 class="back-tagline">A practical guide on how to win more matches by becoming a more efficient and effective competitor.</h2>
  <div class="back-rule"></div>

  <div class="blurb">
    <p>As a tennis player you have the ability to play better matches and win more of them. The Craft of Rally Mastery gives you a system to improve. We start with the individual game of the set itself. Our system examines your physical and mental progression, enabling you to upgrade your movement and performance from shot to shot and point to point. Our system seamlessly integrates the technical (physical) aspects with the tactical (mental/emotional) components, providing a comprehensive approach to elevate this performance.</p>
    <p>We aim to give you much more than how to hit great shots. Irrespective of your current skill level, we will provide you with a detailed strategic and tactical plan to enhance your performance, leading to improved results and increased success in your matches.</p>
    <p>The Craft of Rally Mastery emphasizes the importance of shifting focus from oneself to the opponent, encouraging players to analyze and understand their adversaries. By bringing the opponent back to the forefront of their thinking, the player creates the best possible context in which to improve as a competitor.</p>
    <p>In this book, we present a groundbreaking approach to tennis data analytics that seamlessly integrates match performance with practice sessions, and vice versa.</p>
  </div>

  <div class="author-photo first" role="img" aria-label="Portrait photo of author Corwin Haldane on a tennis court"></div>
  <p class="author-bio first"><span class="author-name">Corwin Haldane</span> is regarded as one of the leading strategy and tactical coaches in the world today. He is the Creator of Racket GridDrill, the world's first Tennis Tracking App that maps and charts match play based on the rally length of a point. Corwin is a Best Selling Author of the book "5 Baseline Habits to Unlock Your Flow Rhythm" and the Co-Founder of The Craft of Rally Mastery promoting coach, player, and parent development. He is often sought after by coaches around the world to design the practice court in a way that revolutionizes a player's mindset to successfully negotiate the pressures of competitive match play.</p>

  <div class="author-photo second" role="img" aria-label="Portrait photo of author Milo Brennick outdoors"></div>
  <p class="author-bio second"><span class="author-name">Milo Brennick</span> is a writer and tennis coach. He is a Co-Founder at The Craft of Rally Mastery and has been working to create a theoretical framework for tennis players of all levels to improve. Milo studies the forces that act on the player during a tennis match (both internal and external) and works with players to meet the challenge these forces represent. He runs online and on court programs designed specifically to improve a player's Competitive Intelligence.</p>

  <div class="app-mark">
    <span class="app-mark-dot"></span>
    <span class="app-mark-name">Racket GridDrill</span>
  </div>
  <div class="back-links">
    <div>www.elevatedrillzone.com</div>
    <div>www.craftofrallymastery.com</div>
  </div>
</section>

<section class="cover front-cover" aria-label="Front cover">
  <svg class="front-art" width="497" height="771" viewBox="0 0 497 771">
    <defs>
      <linearGradient id="topBar" x1="0" y1="0" x2="1" y2="0">
        <stop offset="0" stop-color="#005bb5"/>
        <stop offset="0.4" stop-color="#12b0f0"/>
        <stop offset="1" stop-color="#005bb5"/>
      </linearGradient>
      <linearGradient id="courtPhoto" x1="0" y1="1" x2="1" y2="0">
        <stop offset="0" stop-color="#2f7fd0"/>
        <stop offset="0.6" stop-color="#3d8fdc"/>
        <stop offset="1" stop-color="#7fa24a"/>
      </linearGradient>
      <linearGradient id="ribbonArea" x1="0" y1="0" x2="1" y2="1">
        <stop offset="0" stop-color="#5f9ad6"/>
        <stop offset="1" stop-color="#f6d269"/>
      </linearGradient>
    </defs>
    <polygon points="0,0 122,0 0,76" fill="var(--yellow-pale)"/>
    <polygon points="0,60 98,0 122,0 0,76" fill="var(--yellow)"/>
    <rect x="49" y="30" width="448" height="17" fill="url(#topBar)"/>
    <polygon points="51,771 497,491 497,531 117,771" fill="var(--yellow-pale)"/>
    <polygon points="90,771 497,515 497,531 117,771" fill="var(--yellow)" opacity="0.55"/>
    <polygon points="497,531 117,771 497,771" fill="url(#courtPhoto)" role="img" aria-label="Photo of a tennis ball resting on a blue hard court"/>
    <rect x="0" y="550" width="212" height="200" fill="url(#ribbonArea)" opacity="0.55" role="img" aria-label="Blue and yellow ribbon graphic with a small tennis ball"/>
  </svg>

  <h1 class="book-title">The Craft of<br>Rally<br>Mastery</h1>
  <div class="title-rule"></div>
  <p class="book-subtitle">Developing a Strategic Advantage Through Competitive Intelligence</p>
  <p class="book-authors">Corwin Haldane<br>&amp; Milo Brennick</p>
</section>

</body>
</html>
```